RWT Fittings Ltd Business Cards

We need a business card with our business logo. We provide window and door installations on high-rises in west coast British Colombia, Canada.

I would like my business information and details on one side of the card, and the other side the company name with logo

Target Market(s)

General Contractors

Industry/Entity Type

Construction

Contact Information for Business Card

one side i want my company name and logo in the dark theme logo that i provided

Requirements
Must have
• Marco Peltieri, 16045518293, RWTFittings@mailbox-demo.com, 1407-5194 Linden Row Burnaby BC, V5H 2K9, Owner & Manager

```html
<!DOCTYPE html>
<html lang="en">
<head>
<meta charset="UTF-8">
<title>RWT Fittings Ltd Business Cards</title>
<link rel="stylesheet" href="https://fonts.googleapis.com/css2?family=Montserrat:wght@400;500;700&display=swap">
<style>
  :root {
    --backdrop: #e4e4e6;
    --card-white: #ffffff;
    --card-black: #1d1d1f;
    --brand-blue: #27a7df;
    --brand-grey: #8e8e8e;
    --line-grey: #9a9a9a;
    --ink: #1f1f1f;
    --back-mark: #3b3b3e;
  }
  * { box-sizing: border-box; margin: 0; padding: 0; }
  html, body {
    width: 1200px; height: 786px; overflow: hidden;
    background: var(--backdrop);
    font-family: "Montserrat", sans-serif;
  }
  .stage {
    position: relative; width: 1200px; height: 786px;
    display: flex; align-items: center; justify-content: center; gap: 50px;
  }
  .card {
    position: relative; width: 525px; height: 300px; overflow: hidden;
    box-shadow: 0 6px 18px rgba(0,0,0,0.18);
  }
  .card--front { background: var(--card-white); }
  .card--back { background: var(--card-black); display: flex; align-items: center; justify-content: center; }

  .brand { display: flex; align-items: center; gap: 12px; }
  .brand__square { width: 30px; height: 30px; background: var(--brand-grey); }
  .brand__name { font-weight: 700; font-size: 30px; color: var(--brand-blue); letter-spacing: 0.5px; }
  .card--front .brand { position: absolute; left: 80px; top: 46px; }
  .card--back .brand__square { background: var(--back-mark); width: 34px; height: 34px; }
  .card--back .brand__name { color: var(--back-mark); font-size: 34px; }

  .swoosh { position: absolute; left: 0; bottom: 0; width: 525px; height: 100px; z-index: 0; }

  .holder { position: absolute; left: 60px; top: 152px; text-align: right; width: 172px; z-index: 1; }
  .holder__name { font-weight: 700; font-size: 21px; color: var(--brand-blue); white-space: nowrap; }
  .holder__role { font-weight: 500; font-size: 11.5px; color: var(--ink); margin-top: 3px; }

  .divider { position: absolute; left: 252px; top: 128px; width: 1.5px; height: 82px; background: var(--brand-blue); z-index: 1; }

  .contact { position: absolute; left: 268px; top: 128px; font-size: 11px; color: var(--ink); line-height: 1.3; z-index: 1; }
  .contact__address { margin-bottom: 10px; }
  .contact__row { display: flex; align-items: center; gap: 7px; margin-bottom: 6px; white-space: nowrap; }
  .contact__icon { width: 12px; height: 12px; flex: none; }
</style>
</head>
<body>
<main class="stage">
  <section class="card card--front">
    <svg class="swoosh" viewBox="0 0 525 100" preserveAspectRatio="none">
      <path fill="#27a7df" d="M0 52 C 200 62, 400 52, 525 22 L525 100 L0 100 Z"/>
      <path fill="none" stroke="#9a9a9a" stroke-width="2.5" d="M30 48 C 230 52, 400 38, 510 10"/>
    </svg>

    <div class="brand">
      <span class="brand__square"></span>
      <span class="brand__name">RWT Fittings Ltd</span>
    </div>

    <div class="holder">
      <p class="holder__name">Marco Peltieri</p>
      <p class="holder__role">Owner &amp; Manager</p>
    </div>

    <span class="divider"></span>

    <div class="contact">
      <p class="contact__address">1407-5194 Linden Row<br>Burnaby BC, V5H 2K9</p>
      <p class="contact__row">
        <svg class="contact__icon" viewBox="0 0 24 24"><path fill="#27a7df" d="M6.6 10.8a15.1 15.1 0 0 0 6.6 6.6l2.2-2.2c.3-.3.7-.4 1-.2 1.1.4 2.3.6 3.6.6.6 0 1 .4 1 1V20c0 .6-.4 1-1 1A17 17 0 0 1 3 4c0-.6.4-1 1-1h3.5c.6 0 1 .4 1 1 0 1.3.2 2.5.6 3.6.1.3 0 .7-.2 1z"/></svg>
        16045518293
      </p>
      <p class="contact__row">
        <svg class="contact__icon" viewBox="0 0 24 24"><path fill="#27a7df" d="M2 5h20v14H2z"/><path fill="none" stroke="#fff" stroke-width="2" d="M2 6l10 7 10-7"/></svg>
        RWTFittings@mailbox-demo.com
      </p>
    </div>
  </section>

  <section class="card card--back">
    <div class="brand">
      <span class="brand__square"></span>
      <span class="brand__name">RWT Fittings Ltd</span>
    </div>
  </section>
</main>
</body>
</html>
```